Hi Designers,

I will need 4 web pages designed. The web page looks like an App (if you click on the logo, or the icon on an iPad, it will take you to the website), but it is still a webpage.

Please check the attachment on this brief to understand what specific pages I need to be designed.

A .PSD (straight-up PhotoShop image) as final deliverable is fine, as long as you give us the exact “web color numbers”.

The design is for desktop and iPad but in a single unified web application, NOT separate web app and (native) iPad app.

Details:

Brightwater Policy Partners is developing a browser-based application for use on any mobile device or desktop. The app will be used by corporations to communicate with their employees regarding legal, regulatory and company requirements for conducting business. The app is known as “Harbor Guidance Portal.” When the user clicks on the icon for Harbor Guidance Portal, they will enter a site full of information that a company deems necessary for the employee to do his/her job. There are several content sections within the site, including a login page, training, policies, forms, news feeds and blogs.

The application has been built using Microsoft .NET, and fully supports CSS-type skinning; it uses traditional page layouts. We are seeking a product logo concept (image), a master application/desktop icon (image), as well as a full color scheme/theme/skin design for all areas of the application (header area, body text, menu bar, etc.) in the form of a CSS. The look should be clean, crisp and professional; nothing cartoony or whimsical. It should be easy to read and “airy”.

We have sketched prototypes for the basic application page layout that we can send as a next step of the process.
Updates

Screen shots have been uploaded to this project.  Please use them to guide your design.

Dear designers,

I apologize for the delay in providing feedback. My partners and I will provide feedback in a few days. Thank you for your patience.

Industry/Entity Type

Business

Font styles to use
Other font styles liked:
• see font on screen shots when uploaded

```html
<!DOCTYPE html>
<html lang="en">
<head>
<meta charset="utf-8">
<title>Harbor Guidance Portal</title>
<link rel="stylesheet" href="https://fonts.googleapis.com/css2?family=Roboto:ital,wght@0,400;0,500;0,700;1,400&display=swap">
<style>
:root{
  --bg-top:#0f4384;
  --bg-bottom:#06285a;
  --nav-top:#1f78d0;
  --nav-bottom:#1560b4;
  --panel-bg:#fbfaf7;
  --head-dark-top:#5a5a5a;
  --head-dark-bottom:#3b3b3b;
  --head-green-top:#8cc63f;
  --head-green-bottom:#6aa823;
  --head-orange-top:#f0885a;
  --head-orange-bottom:#d8582a;
  --link:#1560b4;
  --text:#3c3c3c;
  --muted:#7a7a7a;
  --accent-red:#c8461e;
  --badge:#8cc63f;
  --date:#1560b4;
  --rule:#e3e1dc;
  --footer:#2c6fc0;
}
*{box-sizing:border-box;margin:0;padding:0}
html,body{width:1200px;height:1076px;overflow:hidden}
body{
  font-family:"Roboto",Arial,sans-serif;
  background:radial-gradient(ellipse at 50% 0%,var(--bg-top) 0%,var(--bg-bottom) 85%);
  position:relative;color:var(--text);
}
a{text-decoration:none;color:var(--link)}

.brand{position:absolute;left:457px;top:30px;display:flex;align-items:center;gap:16px}
.brand-dot{width:74px;height:74px;border-radius:50%;background:#2a9fd8}
.brand-name{color:#fff;font-size:30px;font-weight:500;letter-spacing:.5px;line-height:1}

.navbar{position:absolute;left:130px;top:125px;width:940px;height:63px;
  background:linear-gradient(var(--nav-top),var(--nav-bottom));box-shadow:0 2px 6px rgba(0,0,0,.35)}
.nav-item{position:absolute;top:10px;width:96px;margin-left:-48px;text-align:center;color:#fff;font-size:12px;letter-spacing:.4px}
.nav-item svg{display:block;margin:0 auto 5px;height:24px}
.search{position:absolute;left:441px;top:16px;width:242px;height:31px;background:#fff;border-radius:2px;
  font-size:11px;font-style:italic;color:#8a8a8a;padding:9px 12px}
.search svg{position:absolute;right:4px;top:7px}
.points{position:absolute;left:728px;top:-7px;width:62px;height:62px}
.points span{position:absolute;left:0;right:0;top:9px;text-align:center;color:#fff;font-size:19px;font-weight:500}
.user{position:absolute;left:808px;top:22px;color:#fff;font-size:13px;display:flex;align-items:center;gap:8px}

.panel{position:absolute;background:var(--panel-bg);box-shadow:0 2px 5px rgba(0,0,0,.35)}
.panel-head{height:44px;display:flex;align-items:center;gap:9px;padding:0 14px;color:#fff;font-size:17px;letter-spacing:.3px}
.head-dark{background:linear-gradient(var(--head-dark-top),var(--head-dark-bottom))}
.head-green{background:linear-gradient(var(--head-green-top),var(--head-green-bottom));font-size:18px}
.head-orange{background:linear-gradient(var(--head-orange-top),var(--head-orange-bottom))}

.news-item{height:79px;border-bottom:1px solid var(--rule);display:flex;gap:12px;padding:14px 10px}
.news-item:last-child{border-bottom:none}
.date{width:44px;height:45px;background:var(--date);color:#fff;font-size:13px;text-align:center;line-height:17px;padding-top:5px;flex:none}
.news-title{font-size:13px;line-height:17px;color:var(--link)}
.more{font-size:11px;font-style:italic;color:var(--muted);margin-top:5px}

.photo{background:linear-gradient(135deg,#b88c5c,#d9c3a2 50%,#7f8fa8)}
.doc-photo{margin:12px 12px 0;height:134px}
.doc-title{font-size:13px;color:var(--link);margin:12px 12px 6px}
.doc-text{font-size:11px;font-style:italic;color:var(--muted);line-height:21px;margin:0 12px}

.blog-photo{margin:10px 11px 0;height:161px;border:2px solid #c9cdd4;
  background:radial-gradient(circle at 50% 35%,#e8f0fb 0%,#8aa2c4 18%,#3d5477 55%,#22324a 100%)}
.blog-title{font-size:19px;color:var(--link);margin:14px 13px 6px}
.blog-text{font-size:13px;line-height:23px;margin:0 13px}
.blog-meta{font-size:13px;color:var(--accent-red);margin:10px 13px}

.link-list{list-style:none;padding:12px 14px}
.link-list li{height:31px;display:flex;align-items:center;gap:6px;font-size:13px;letter-spacing:.2px}
.dot{width:15px;height:15px;border-radius:50%;flex:none;display:flex;align-items:center;justify-content:center;color:#fff;font-size:9px;font-weight:700}
.dot-green{background:#3a8a6a}.dot-blue{background:#1a4f8f}.dot-orange{background:#e07a2a}.dot-red{background:#c21e4a}

.report-item{height:80px;border-bottom:1px solid var(--rule);display:flex;gap:10px;padding:12px 8px}
.report-item:last-child{border-bottom:none}
.thumb{width:48px;height:48px;background:#fff;border:1px solid #cfd3d8;flex:none;margin-top:2px}
.report-title{font-size:13px;color:var(--link);margin-bottom:4px}
.report-text{font-size:11px;line-height:18px}

.faq-item{border-bottom:1px solid var(--rule);padding:10px 19px 0}
.faq-q{font-size:13px;line-height:17px;color:var(--link)}
.faq-a{font-size:11px;line-height:17px;margin-top:1px}

.footer-rule{position:absolute;left:100px;top:968px;width:1000px;height:8px;
  background:radial-gradient(ellipse at center,rgba(0,0,0,.45),transparent 70%)}
.footer{position:absolute;top:1013px;left:0;right:0;text-align:center;color:var(--footer);font-size:13px;line-height:21px;letter-spacing:.3px}
</style>
</head>
<body>

<header class="brand">
  <div class="brand-dot"></div>
  <div class="brand-name">Harbor Guidance Portal</div>
</header>

<nav class="navbar">
  <a class="nav-item" style="left:48px" href="#">
    <svg width="22" viewBox="0 0 22 22"><path d="M11 2 1 11h3v9h5v-6h4v6h5v-9h3z" fill="#fff"/></svg>HOME</a>
  <a class="nav-item" style="left:144px" href="#">
    <svg width="30" viewBox="0 0 30 22"><g fill="#fff"><rect x="0" y="3" width="4" height="3"/><rect x="6" y="3" width="24" height="3"/><rect x="0" y="9" width="4" height="3"/><rect x="6" y="9" width="24" height="3"/><rect x="0" y="15" width="4" height="3"/><rect x="6" y="15" width="24" height="3"/></g></svg>MENU</a>
  <a class="nav-item" style="left:245px" href="#">
    <svg width="34" viewBox="0 0 34 22"><path d="M8 3h18c4 0 7 6 8 14 0 4-4 5-6 2l-3-4H9l-3 4c-2 3-6 2-6-2C1 9 4 3 8 3z" fill="#fff"/><g fill="#1766bb"><rect x="7" y="8" width="6" height="2"/><rect x="9" y="6" width="2" height="6"/><circle cx="24" cy="8" r="1.3"/><circle cx="27" cy="11" r="1.3"/></g></svg>GAME</a>
  <a class="nav-item" style="left:341px" href="#">
    <svg width="22" viewBox="0 0 22 22"><g fill="#fff"><rect x="1" y="1" width="5" height="20"/><rect x="8" y="6" width="5" height="15"/><rect x="15" y="12" width="6" height="9"/></g></svg>HCP 360</a>
  <div class="search">Search...
    <svg width="18" height="18" viewBox="0 0 18 18"><circle cx="7" cy="7" r="5" fill="none" stroke="#333" stroke-width="2"/><path d="M11 11l6 6" stroke="#4a2a6a" stroke-width="3"/></svg>
  </div>
  <div class="points">
    <svg width="62" height="62" viewBox="0 0 62 62"><path d="M0 0h62v40L31 62 0 40z" fill="var(--badge)"/></svg>
    <span>475</span>
  </div>
  <div class="user">
    <svg width="20" height="18" viewBox="0 0 20 18"><circle cx="10" cy="5" r="4.5" fill="#fff"/><path d="M1 18c0-6 4-8 9-8s9 2 9 8z" fill="#fff"/></svg>
    Dana Hale
    <svg width="12" height="7" viewBox="0 0 12 7" style="margin-left:6px"><path d="M0 0h12L6 7z" fill="#fff"/></svg>
  </div>
</nav>

<section class="panel" style="left:130px;top:205px;width:221px;height:279px">
  <div class="panel-head head-dark">
    <svg width="26" height="20" viewBox="0 0 26 20"><path d="M3 8h5l11-6v16L8 12H3z" fill="#e23b2a"/><rect x="5" y="12" width="4" height="6" fill="#bbb"/></svg>
    Compliance News</div>
  <div class="news-item"><div class="date">Nov<br>18</div><div><div class="news-title">Sed ut perspiciatis unde omnis</div><div class="more">Read More</div></div></div>
  <div class="news-item"><div class="date">Nov<br>18</div><div><div class="news-title">Sed ut perspiciatis unde omnis</div><div class="more">Read More</div></div></div>
  <div class="news-item"><div class="date">Nov<br>18</div><div><div class="news-title">Sed ut perspiciatis unde omnis</div><div class="more">Read More</div></div></div>
</section>

<section class="panel" style="left:130px;top:495px;width:221px;height:422px">
  <div class="panel-head head-dark">
    <svg width="18" height="18" viewBox="0 0 18 18"><rect x="1" y="11" width="16" height="5" fill="#3a7ac8"/><rect x="2" y="6" width="14" height="5" fill="#e0a030"/><rect x="1" y="1" width="16" height="5" fill="#5aa03a"/></svg>
    Document Library</div>
  <div class="photo doc-photo" role="img" aria-label="Students reading at tables in a library"></div>
  <div class="doc-title">Sed ut perspiciatis unde omnis</div>
  <p class="doc-text">Lorem ipsum dolor sit amet, consectetur adipisicing eitseo eiusmod tempor incididunt ut labore et dolore magna aliqua.Lorem ipsum dolor sit amet, consectetur adipisicing eitseo eiusmod tempor incididunt ut labore et dolore magna aliqua.</p>
</section>

<section class="panel" style="left:360px;top:205px;width:480px;height:368px">
  <div class="panel-head head-green">
    <svg width="24" height="22" viewBox="0 0 24 22"><circle cx="11" cy="11" r="10" fill="#3aa8d8"/><rect x="5" y="8" width="12" height="2" fill="#fff"/><rect x="5" y="12" width="9" height="2" fill="#fff"/></svg>
    Compliance Blog</div>
  <div class="blog-photo" role="img" aria-label="Hand touching a glowing digital interface"></div>
  <h2 class="blog-title" style="font-weight:400">Sed ut perspiciatis unde omnis</h2>
  <p class="blog-text">Lorem ipsum dolor sit amet, consectetur adipisicing eitseo eiusmod tempor incididunt ut labore et dolore magna aliqua.Sed ut perspiciatis unde omnis iste natus error sit voluptatem accusantium...</p>
  <div class="blog-meta">Read More &nbsp;|&nbsp; Posted on 2 days...</div>
</section>

<section class="panel" style="left:360px;top:588px;width:235px;height:329px">
  <div class="panel-head head-orange">
    <svg width="24" height="22" viewBox="0 0 24 22"><g fill="none" stroke="#d8c040" stroke-width="3"><rect x="2" y="10" width="11" height="6" rx="3" transform="rotate(-40 7 13)"/><rect x="10" y="5" width="11" height="6" rx="3" transform="rotate(-40 15 8)"/></g></svg>
    Relevant Links</div>
  <ul class="link-list">
    <li><span class="dot dot-green">✎</span>Sed ut perspiciatis unde</li>
    <li><span class="dot dot-blue">▪</span>Duis aute irure dolor</li>
    <li><span class="dot dot-orange">◂</span>dolore magna aliqua</li>
    <li><span class="dot dot-red">?</span>Sed ut perspiciatis unde</li>
    <li><span class="dot dot-green">✎</span>Duis aute irure dolor</li>
    <li><span class="dot dot-blue">▪</span>dolore magna aliqua</li>
    <li><span class="dot dot-orange">◂</span>Sed ut perspiciatis unde</li>
    <li><span class="dot dot-red">?</span>Duis aute irure dolor</li>
  </ul>
</section>

<section class="panel" style="left:606px;top:588px;width:235px;height:329px">
  <div class="panel-head head-orange">
    <svg width="20" height="22" viewBox="0 0 20 22"><path d="M2 1h11l5 5v15H2z" fill="#fff"/><g fill="#3a7ac8"><rect x="5" y="8" width="10" height="2"/><rect x="5" y="12" width="10" height="2"/><rect x="5" y="16" width="7" height="2"/></g></svg>
    Forms</div>
  <ul class="link-list">
    <li><span class="dot dot-green">✎</span>Sed ut perspiciatis unde</li>
    <li><span class="dot dot-blue">▪</span>Duis aute irure dolor</li>
    <li><span class="dot dot-orange">◂</span>dolore magna aliqua</li>
    <li><span class="dot dot-red">?</span>Sed ut perspiciatis unde</li>
    <li><span class="dot dot-green">✎</span>Duis aute irure dolor</li>
    <li><span class="dot dot-blue">▪</span>dolore magna aliqua</li>
    <li><span class="dot dot-orange">◂</span>Sed ut perspiciatis unde</li>
    <li><span class="dot dot-red">?</span>Duis aute irure dolor</li>
  </ul>
</section>

<section class="panel" style="left:850px;top:205px;width:221px;height:279px">
  <div class="panel-head head-dark">
    <svg width="22" height="20" viewBox="0 0 22 20"><rect x="1" y="8" width="5" height="12" fill="#e04a3a"/><rect x="8" y="3" width="5" height="17" fill="#8cc63f"/><rect x="15" y="10" width="5" height="10" fill="#3aa8d8"/></svg>
    Reports</div>
  <div class="report-item">
    <svg class="thumb" viewBox="0 0 48 48"><g fill="#8ab0d8"><rect x="6" y="8" width="36" height="4"/><rect x="6" y="16" width="36" height="3"/><rect x="6" y="22" width="36" height="3"/><rect x="6" y="28" width="36" height="3"/><rect x="6" y="34" width="36" height="3"/></g></svg>
    <div><div class="report-title">Perspiciatis unde</div><div class="report-text">Eiusmod tempor incidi-<br>dunt ut labore..</div></div>
  </div>
  <div class="report-item">
    <svg class="thumb" viewBox="0 0 48 48"><path d="M30 16V6a10 10 0 0 1 10 10z" fill="#e04a3a"/><path d="M30 16h10a10 10 0 1 1-10-10z" fill="#3aa8d8"/><g fill="#8cc63f"><rect x="8" y="32" width="4" height="10"/><rect x="15" y="26" width="4" height="16"/><rect x="22" y="34" width="4" height="8"/></g></svg>
    <div><div class="report-title">Perspiciatis unde</div><div class="report-text">Eiusmod tempor incidi-<br>dunt ut labore..</div></div>
  </div>
  <div class="report-item">
    <svg class="thumb" viewBox="0 0 48 48"><g stroke-width="3"><path d="M6 34 20 22l10 6 12-14" stroke="#e04a3a" fill="none"/><path d="M6 40 20 30l10 4 12-8" stroke="#3a7ac8" fill="none"/></g></svg>
    <div><div class="report-title">Perspiciatis unde</div><div class="report-text">Eiusmod tempor incidi-<br>dunt ut labore..</div></div>
  </div>
</section>

<section class="panel" style="left:850px;top:495px;width:221px;height:422px">
  <div class="panel-head head-dark">
    <svg width="30" height="20" viewBox="0 0 30 20"><ellipse cx="12" cy="9" rx="11" ry="7" fill="#f0b020"/><ellipse cx="19" cy="12" rx="10" ry="6" fill="#f8d030"/></svg>
    FAQ’s</div>
  <div class="faq-item" style="height:89px"><div class="faq-q">Sed ut perspiciatis unde omnis?</div><div class="faq-a">Veritatis et quasi architecto beatae vitae dicta sunt...</div></div>
  <div class="faq-item" style="height:92px"><div class="faq-q">Sed ut perspiciatis unde omnis?</div><div class="faq-a">Veritatis et quasi architecto beatae vitae dicta sunt...</div></div>
  <div class="faq-item" style="height:94px"><div class="faq-q">Sed ut perspiciatis unde omnis?</div><div class="faq-a">Veritatis et quasi architecto beatae vitae dicta sunt...</div></div>
  <div class="faq-item" style="border-bottom:none"><div class="faq-q">Sed ut perspiciatis unde omnis?</div><div class="faq-a">Veritatis et quasi architecto beatae vitae dicta sunt...</div></div>
</section>

<div class="footer-rule"></div>
<footer class="footer">Copyright © 2013. Harbor Guidance Portal<br>All Right Reserved</footer>

</body>
</html>
```